Corwin Beacon Lighting - Commercial & Residential Landscape Lighting

Landscape Lighting Services & Design: Create a website for our landscape lighting company. We would like the design to be tailored around this description:
Illuminate with Confidence. Designed with Precision. Installed with Care.
Locally and veteran-owned, we take pride in transforming outdoor spaces through innovative lighting solutions tailored to your vision. From landscape and holiday lighting to permanent installations, our effortless process and expert design deliver breathtaking results and lasting curb appeal. Backed by a lifetime warranty and quarterly service options, our commitment to quality and customer satisfaction is unwavering. Try before you buy and experience your home in a whole new light with our complimentary demo kit — see the stunning effects before you decide.
- Also, add in this information as well; Outdoor Lighting not only beautifies spaces but also significantly enhances safety by illuminating your home or business. Beautifully lit entrances deter potential intruders, making your home a safer place for your loved ones. we also offer quarterly service plans to ensure lighting equipment continues to operate & illuminate effectively throughout the year. Also mention we provide free estimates and we are offering a 10% discount to military, veterans, and first responders.

Target Market(s)

Luxury market

Industry/Entity Type

Landscape Lighting - Residential & Commercial Lighting Services

Coding

Coded - Design and coding required

Number of Pages Required

2 page

Colors
00AB8E
00BBA5
67D7C9
C6EFE9
E9F9F6
59FF00
82FF00
B8FF75
E3FFCB
F4FFEA
FFC000
F8CF3A
FAE287
FDF2CF
FEFAEE

Requirements
Must have
• a lead generation button where people can submit their information for us to reach out to them and schedule their free estimate, homepage, about page, contact page, products and services page, user friendly, easy to navigate, and it also must be engaging and eye popping, as well as appealing to the luxury market. Please use colors; verdent green, dark green, ivory, and sunny yellow. Also, include an about page that references our story; Derek is retired Army and he opened a fitness studio in 2017 with his wife Jolene. He has installed low voltage lighting in every home he lived in and for his friends and family over the years and decided to open his own business because he is passionate about beautifying outdoor landscapes and highlighting a properties full potential, not only in the day but at night as well all while providing safety and security for his clients. Having a deep respect for nature and landscaping, he wants to provide the same care and quality to each of his clients as he has in the fitness industry for decades. He believes small businesses are the back bone of America and he's excited to provide a service that is all to often neglected in the design of a home.
Nice to have
• I would like to have a clear intent and purpose, engaging web design, clear call to action, optimized for search engines, mobile friendy design, security measures, credibility indicators

```html
<!DOCTYPE html>
<html lang="en">
<head>
<meta charset="utf-8">
<title>Corwin Beacon Lighting – Landscape Lighting</title>
<link rel="stylesheet" href="https://fonts.googleapis.com/css2?family=Jost:wght@400;500;700;800&family=Mulish:wght@400;600;700&display=swap">
<style>
:root{
  --ink:#121212;
  --text:#6d6d6d;
  --gold-a:#f3a81c;
  --gold-b:#f8cf3a;
  --accent:#b3320c;
  --teal:#1aa386;
  --teal-deep:#12997d;
  --ivory:#fefde8;
  --sun:#f9b72b;
  --line:#bdb89f;
  --white:#ffffff;
}
*{margin:0;padding:0;box-sizing:border-box}
html,body{width:1200px;height:3920px;overflow:hidden}
body{position:relative;background:var(--white);font-family:"Mulish",sans-serif;color:var(--text)}
.abs{position:absolute}
.btn{position:absolute;display:flex;align-items:center;justify-content:center;border-radius:26px;font-family:"Mulish",sans-serif;font-weight:700;font-size:13px;letter-spacing:.2px;color:var(--white);text-transform:uppercase;background:linear-gradient(90deg,var(--gold-b),var(--gold-a));box-shadow:0 4px 8px rgba(0,0,0,.12)}
.btn-teal{background:var(--teal)}
.btn-ghost{background:var(--white);color:var(--teal);border:1.5px solid #a9c9bf;box-shadow:none}
.heading{position:absolute;font-family:"Jost",sans-serif;font-weight:400;font-size:42px;color:var(--ink);letter-spacing:.5px;text-transform:uppercase}
.heading span{color:var(--accent)}
.copy{position:absolute;font-size:14.5px;line-height:27.2px;text-align:justify}
.brand-name{font-family:"Jost",sans-serif;font-weight:500;color:var(--gold-a);text-transform:uppercase;letter-spacing:3px;line-height:1.1}

/* hero */
.hero{position:absolute;left:0;top:0;width:1200px;height:700px;clip-path:polygon(0 0,100% 0,100% 700px,0 601px);background:linear-gradient(115deg,#0b0c10 0%,#15171c 28%,#3a2a1f 48%,#7a4a2b 62%,#b07a3c 72%,#3a3f33 88%,#171a1a 100%)}
.hero .brand{left:141px;top:54px;width:230px;font-size:26px}
.call{left:795px;top:33px;display:flex;align-items:center;gap:8px;color:var(--white);font-weight:600;font-size:17px}
.call i{width:22px;height:22px;border-radius:50%;background:var(--teal);display:block}
.nav{left:560px;top:72px;display:flex;align-items:center;height:42px}
.nav a{color:var(--white);font-weight:700;font-size:13px;text-transform:uppercase;text-decoration:none;margin-right:33px}
.nav a.active{background:var(--sun);padding:0 18px;height:42px;display:flex;align-items:center;clip-path:polygon(20% 0,100% 0,100% 100%,0 100%);padding-left:30px;margin-right:26px}
.hero-title{left:141px;top:236px;font-family:"Jost",sans-serif;color:var(--white);font-size:42px;line-height:56px;text-transform:uppercase;text-shadow:0 2px 6px rgba(0,0,0,.5)}
.hero-title b{font-weight:800}
.hero-title em{font-style:normal;font-weight:500}
.play{left:1107px;top:548px;width:38px;height:38px;border-radius:50%;background:var(--white);display:flex;align-items:center;justify-content:center}

/* about */
.about-art{left:84px;top:660px;width:400px;height:537px;border-radius:200px 200px 10px 10px;background:linear-gradient(180deg,#6f8fc2 0%,#27344a 35%,#2e3b2a 65%,#1d2a17 100%)}

/* products */
.products{left:0;top:1141px;width:1200px;height:820px;background:var(--ivory);clip-path:polygon(0 71px,100% 0,100% 100%,0 100%)}
.card{position:absolute;top:1380px;width:290px;height:422px}
.card svg{position:absolute;left:0;top:0}
.card .pic{position:absolute;left:69px;top:36px;width:152px;height:152px;border-radius:50%}
.card h3{position:absolute;left:0;top:210px;width:290px;text-align:center;font-family:"Mulish",sans-serif;font-weight:600;font-size:15.5px;color:var(--ink);text-transform:uppercase}
.card p{position:absolute;left:38px;top:242px;width:214px;text-align:center;font-size:13.5px;line-height:23.5px;color:var(--text)}
.card .btn{left:79px;top:325px;width:132px;height:49px}
.arrow{position:absolute;top:1554px;width:44px;height:44px;border-radius:50%;border:1.5px solid #9a9a8e;background:var(--white);display:flex;align-items:center;justify-content:center}

/* demo band */
.demo{left:0;top:1875px;width:1200px;height:379px;background:var(--sun);clip-path:polygon(0 67px,100% 0,100% 100%,0 100%)}
.demo-text{left:0;top:1990px;width:1200px;text-align:center;font-family:"Jost",sans-serif;font-weight:500;font-size:33px;line-height:39px;color:var(--white)}

/* story */
.photo{position:absolute;border-radius:50%}

/* offer */
.offer{left:144px;top:2771px;width:912px;height:232px;border-radius:16px;background:var(--teal-deep)}
.offer-text{left:144px;top:2800px;width:912px;text-align:center;font-family:"Jost",sans-serif;font-weight:500;font-size:33px;line-height:40px;color:var(--white)}

/* footer */
.footer{left:0;top:3445px;width:1200px;height:475px;background:#000;clip-path:polygon(0 114px,100% 0,100% 100%,0 100%)}
.footer .brand{left:0;top:3588px;width:1200px;text-align:center;font-size:32px}
.contact{position:absolute;top:3700px;display:flex;align-items:center;gap:12px;color:var(--white);font-size:14px;line-height:20px}
.contact .ring{width:44px;height:44px;border-radius:50%;border:2px solid var(--white);display:flex;align-items:center;justify-content:center;flex:none}
.contact .ring.fill{background:var(--teal);border-color:var(--teal)}
.legal{left:0;top:3780px;width:1200px;text-align:center;color:var(--white);font-size:14px}
.social{left:551px;top:3823px;display:flex;gap:9px}
.social i{display:block;width:26px;height:26px;border-radius:50%;background:var(--white)}
.social i.on{background:var(--sun)}
</style>
</head>
<body>

<!-- HERO -->
<section class="hero" role="img" aria-label="Brick home at dusk with warm landscape uplighting along the garden beds">
</section>
<div class="abs hero-block">
  <div class="abs brand brand-name" style="left:141px;top:52px;width:240px;font-size:26px">Corwin Beacon Lighting</div>
</div>
<div class="abs call"><i></i>CALL US : +1 555 014 2290</div>
<nav class="abs nav">
  <a class="active" href="#">Home</a>
  <a href="#">About Us</a>
  <a href="#">Products &amp; Services</a>
  <a href="#" style="margin-right:0">Contact Us</a>
</nav>
<h1 class="abs hero-title"><b>Illuminate with confidence.</b><br><em>Designed with precision.</em><br><b>Installed with care.</b></h1>
<a class="btn" style="left:141px;top:437px;width:247px;height:48px">Schedule a free estimate</a>
<div class="abs play"><svg width="16" height="16" viewBox="0 0 16 16"><path d="M4 2 L14 8 L4 14 Z" fill="none" stroke="#222" stroke-width="1.8"/></svg></div>

<!-- ABOUT -->
<div class="abs about-art" role="img" aria-label="Bulb-shaped frame showing a lit front yard at night"></div>
<h2 class="heading" style="left:547px;top:770px">About <span>Us</span></h2>
<p class="copy" style="left:547px;top:832px;width:507px">Locally and veteran-owned, we take pride in transforming outdoor spaces through innovative lighting solutions tailored to your vision. From landscape and holiday lighting to permanent installations, our effortless process and expert design deliver breathtaking results and lasting curb appeal. Backed by a lifetime warranty and quarterly service options, our commitment to quality and customer satisfaction is unwavering.</p>
<a class="btn" style="left:547px;top:1033px;width:133px;height:48px">Read more</a>

<!-- PRODUCTS -->
<section class="abs products"></section>
<h2 class="heading" style="left:0;top:1278px;width:1200px;text-align:center">Products &amp; <span>Services</span></h2>

<div class="arrow" style="left:74px"><svg width="14" height="14" viewBox="0 0 14 14"><path d="M9 2 L4 7 L9 12" fill="none" stroke="#333" stroke-width="2"/></svg></div>
<div class="arrow" style="left:1082px"><svg width="14" height="14" viewBox="0 0 14 14"><path d="M5 2 L10 7 L5 12" fill="none" stroke="#333" stroke-width="2"/></svg></div>

<article class="card" style="left:149px">
  <svg width="290" height="422" viewBox="0 0 290 422"><path d="M2 150 C2 62 68 2 145 2 C222 2 288 62 288 150 L257 420 L33 420 Z" fill="none" stroke="var(--line)" stroke-width="2"/></svg>
  <div class="pic" role="img" aria-label="Modern commercial building lit at dusk" style="background:linear-gradient(160deg,#3f7de0,#1c2f5a 60%,#e7a24a)"></div>
  <h3>Commercial Lighting</h3>
  <p>Sed ut perspiciatis unde omnis iste natus error sit emoluptatem accusantium usantiud</p>
  <a class="btn btn-ghost">Read more</a>
</article>
<article class="card" style="left:456px">
  <svg width="290" height="422" viewBox="0 0 290 422"><path d="M2 150 C2 62 68 2 145 2 C222 2 288 62 288 150 L257 420 L33 420 Z" fill="#fff" stroke="var(--line)" stroke-width="2"/></svg>
  <div class="pic" role="img" aria-label="Lounge interior with signature pendant lighting and plants" style="background:linear-gradient(170deg,#e6e3dc,#a9a18e 55%,#5a6b3a)"></div>
  <h3>Signature Lighting</h3>
  <p>Sed ut perspiciatis unde omnis iste natus error sit emoluptatem accusantium usantiud</p>
  <a class="btn">Read more</a>
</article>
<article class="card" style="left:762px">
  <svg width="290" height="422" viewBox="0 0 290 422"><path d="M2 150 C2 62 68 2 145 2 C222 2 288 62 288 150 L257 420 L33 420 Z" fill="none" stroke="var(--line)" stroke-width="2"/></svg>
  <div class="pic" role="img" aria-label="House decorated with warm holiday lights at night" style="background:radial-gradient(circle at 50% 55%,#d98a3c,#6b2a16 55%,#1a0e0b)"></div>
  <h3>Residential Lighting</h3>
  <p>Sed ut perspiciatis unde omnis iste natus error sit emoluptatem accusantium usantiud</p>
  <a class="btn btn-ghost">Read more</a>
</article>

<!-- DEMO KIT -->
<section class="abs demo"></section>
<p class="abs demo-text">Try before you buy and experience your home<br>in a whole new light with our complimentary demo kit<br>see the stunning effects before you decide.</p>
<a class="btn btn-teal" style="left:523px;top:2137px;width:154px;height:49px">Get started</a>

<!-- OUR STORY -->
<h2 class="heading" style="left:157px;top:2352px">Our <span>Story</span></h2>
<p class="copy" style="left:157px;top:2413px;width:454px">Derek is retired Army and he opened a fitness studio in 2017 with his wife Jolene. He has installed low voltage lighting in every home he lived in and for his friends and family over the years and decided to open his own business because he is passionate about beautifying outdoor landscapes and highlighting a properties full potential, not only in the day but at night as well all while providing safety and security for his clients. Having a deep respect for nature and landscaping,</p>
<a class="btn" style="left:157px;top:2653px;width:133px;height:49px">Read more</a>
<div class="photo" role="img" aria-label="Founder working on a laptop in a bright office" style="left:734px;top:2394px;width:314px;height:314px;background:linear-gradient(160deg,#dfe6ea,#8fa7b8 50%,#2f4a6e)"></div>

<!-- OFFER -->
<section class="abs offer"></section>
<p class="abs offer-text">We proudly offer 10% off for all military,<br>veterans, and first responders.</p>
<a class="btn" style="left:479px;top:2914px;width:243px;height:49px">Schedule a free estimate</a>

<!-- WHY US -->
<div class="photo" role="img" aria-label="Home exterior with lit walkway and trees at night" style="left:151px;top:3156px;width:310px;height:310px;background:radial-gradient(circle at 45% 45%,#e6c48a,#46506e 45%,#131a2a)"></div>
<h2 class="heading" style="left:599px;top:3111px">Why <span>Us</span></h2>
<p class="copy" style="left:599px;top:3173px;width:454px">Outdoor Lighting not only beautifies spaces but also significantly enhances safety by illuminating your home or business. Beautifully lit entrances deter potential intruders, making your home a safer place for your loved ones. we also offer quarterly service plans to ensure lighting equipment continues to operate &amp; illuminate effectively throughout the year.</p>
<a class="btn" style="left:599px;top:3366px;width:133px;height:49px">Read more</a>

<!-- FOOTER -->
<footer class="abs footer"></footer>
<div class="abs brand brand-name" style="left:0;top:3590px;width:1200px;text-align:center;font-size:32px">Corwin Beacon<br>Lighting</div>
<div class="contact" style="left:245px">
  <span class="ring"><svg width="14" height="16" viewBox="0 0 14 16"><path d="M7 15 C3 10 1.5 7.5 1.5 5.5 A5.5 5.5 0 0 1 12.5 5.5 C12.5 7.5 11 10 7 15 Z" fill="#fff"/><circle cx="7" cy="5.5" r="2" fill="#000"/></svg></span>
  <span>23,Sed ut perspiciatis unde<br>omnis iste natus,Canada</span>
</div>
<div class="contact" style="left:528px">
  <span class="ring fill"><svg width="16" height="16" viewBox="0 0 16 16"><path d="M3 1.5 L6 1.5 L7 5 L5.2 6.3 C6.2 8.4 7.6 9.8 9.7 10.8 L11 9 L14.5 10 L14.5 13 C14.5 14 13.5 14.6 12.5 14.5 C6.5 13.8 2.2 9.5 1.5 3.5 C1.4 2.5 2 1.5 3 1.5 Z" fill="#fff"/></svg></span>
  <span>+1 555 014 2290</span>
</div>
<div class="contact" style="left:733px">
  <span class="ring"><svg width="14" height="11" viewBox="0 0 14 11"><rect x="0.5" y="0.5" width="13" height="10" rx="1" fill="#fff"/><path d="M1 1 L7 6 L13 1" fill="none" stroke="#000" stroke-width="1.3"/></svg></span>
  <span>hello@corwinbeacon.com</span>
</div>
<p class="abs legal">Copyright 2025 Corwin Beacon Lighting. All Rights Reserved &nbsp;|&nbsp; Privacy Policy &nbsp;|&nbsp; Terms of Use</p>
<div class="abs social" aria-label="Social links">
  <i></i><i class="on"></i><i></i>
</div>

</body>
</html>
```